Business Cards - Brightpath Horizon

need to design unique business card for my mortgage business. I need to design credit card style business card for my business or any unique idea that you might have

Target Market(s)

Home Loan customers

Industry/Entity Type

Mortgage Brokerage

Contact Information for Business Card

please design credit card style or very unique style business card

Colors

Designer to choose colors to be used in the design.

Requirements
Must have
• Name
• position
• Phone number
• fax number
• email address
• website address
• social media address
• All above fields will be provided once design in finalised

```html
<!DOCTYPE html>
<html lang="en">
<head>
<meta charset="utf-8">
<title>Brightpath Horizon – Business Cards</title>
<link href="https://fonts.googleapis.com/css2?family=Playfair+Display:wght@500&family=Lora:ital,wght@0,500;1,500&family=Open+Sans:wght@400;500&display=swap" rel="stylesheet">
<style>
  :root {
    --backdrop: #3a3a3a;
    --card-white: #ffffff;
    --brand-blue: #0632c4;
    --brand-orange: #f28a1a;
    --ink: #1d1d1d;
    --on-blue: #ffffff;
  }
  * { margin: 0; padding: 0; box-sizing: border-box; }
  html, body { width: 1200px; height: 900px; overflow: hidden; }
  body { background: var(--backdrop); position: relative; font-family: "Open Sans", Arial, sans-serif; }

  .card {
    position: absolute;
    top: 170px;
    width: 347px;
    height: 561px;
    overflow: hidden;
    box-shadow: 3px 3px 6px rgba(0, 0, 0, 0.45);
  }
  .card--front { left: 259px; background: var(--card-white); }
  .card--back  { left: 631px; background: var(--brand-blue); }

  .wordmark {
    position: absolute;
    left: 0; right: 0;
    text-align: center;
    font-family: "Playfair Display", Georgia, serif;
    font-weight: 500;
    line-height: 1.05;
    letter-spacing: 1px;
  }
  .wordmark span { display: block; font-size: 38px; }
  .card--front .wordmark { top: 118px; color: var(--brand-blue); }
  .card--back  .wordmark { top: 210px; color: var(--on-blue); }

  .tagline {
    position: absolute;
    left: 0; right: 0;
    text-align: center;
    font-family: "Lora", Georgia, serif;
    font-style: italic;
    font-size: 16px;
  }
  .card--front .tagline { top: 227px; color: var(--brand-orange); }
  .card--back  .tagline { top: 327px; color: var(--on-blue); }

  .holder { position: absolute; top: 336px; left: 0; right: 0; text-align: center; }
  .holder__name {
    font-family: "Lora", Georgia, serif;
    font-weight: 500;
    font-size: 19px;
    letter-spacing: 0.5px;
    color: var(--brand-blue);
  }
  .holder__role { font-size: 14px; color: var(--ink); margin-top: 1px; }

  .contact-icons { position: absolute; top: 393px; left: 0; right: 0; display: flex; justify-content: center; gap: 3px; }
  .contact-icons svg { width: 21px; height: 21px; }

  .contact-list { position: absolute; top: 418px; left: 0; right: 0; text-align: center; list-style: none; font-size: 14px; line-height: 20.5px; color: var(--ink); }

  .social-band {
    position: absolute;
    left: 0; right: 0; bottom: 0;
    height: 62px;
    background: var(--brand-blue);
    display: flex;
    justify-content: center;
    align-items: center;
    gap: 13px;
  }
  .social-band__slot { width: 37px; height: 41px; background: var(--card-white); }

  .website {
    position: absolute;
    top: 504px; left: 0; right: 0;
    text-align: center;
    color: var(--on-blue);
    font-size: 18px;
    letter-spacing: 2.4px;
  }
</style>
</head>
<body>

  <section class="card card--front" aria-label="Business card front">
    <div class="wordmark"><span>BRIGHTPATH</span><span>HORIZON</span></div>
    <p class="tagline">Clear advice, steady home</p>

    <div class="holder">
      <p class="holder__name">DANIEL ASHFORD</p>
      <p class="holder__role">Managing Director</p>
    </div>

    <div class="contact-icons" aria-hidden="true">
      <svg viewBox="0 0 20 20"><circle cx="10" cy="10" r="10" fill="var(--brand-blue)"/><path d="M5 9c0-2 2-3 5-3s5 1 5 3l-2 1-1-2H8l-1 2zM7 11h6l1 3H6z" fill="#fff"/></svg>
      <svg viewBox="0 0 20 20"><circle cx="10" cy="10" r="10" fill="var(--brand-blue)"/><rect x="6" y="5" width="8" height="10" rx="1" fill="#fff"/><rect x="7.5" y="7" width="5" height="2" fill="var(--brand-blue)"/><rect x="7.5" y="10.5" width="5" height="3" fill="var(--brand-blue)"/></svg>
      <svg viewBox="0 0 20 20"><circle cx="10" cy="10" r="10" fill="var(--brand-blue)"/><rect x="5" y="6.5" width="10" height="7" fill="#fff"/><path d="M5 6.5l5 4 5-4" fill="none" stroke="var(--brand-blue)" stroke-width="1"/></svg>
    </div>

    <ul class="contact-list">
      <li>(044)123456789</li>
      <li>(044)123456789</li>
      <li>info@youremail.com</li>
    </ul>

    <div class="social-band">
      <span class="social-band__slot" role="img" aria-label="Social network link"></span>
      <span class="social-band__slot" role="img" aria-label="Social network link"></span>
      <span class="social-band__slot" role="img" aria-label="Social network link"></span>
    </div>
  </section>

  <section class="card card--back" aria-label="Business card back">
    <div class="wordmark"><span>BRIGHTPATH</span><span>HORIZON</span></div>
    <p class="tagline">Clear advice, steady home</p>
    <p class="website">www.websitename.com</p>
  </section>

</body>
</html>
```